Tovimar Community Development Planning New web site

Design a new web site. I have a budget of $1,500.00.
Attached on PowerPoint is a complete site plan. Home page and linked pages.
10 - 12 pages. All copy and photos will be supplied. (300dpi)
I have shown them the concept which they like.
No data bases required. Home page with animations dissolving.
They former web site has been taken down. They have been in business 30 years in New Jersey
Colors teal blues and greens
There will be a new logo)being designed)
The text in home page copy will give you a detailed story what they are all about.

files have been approved for Tovimar, Inc.   Brenton is the designer

```html
<!DOCTYPE html>
<html lang="en">
<head>
<meta charset="utf-8">
<title>Tovimar Inc. — Community Development Planning</title>
<link href="https://fonts.googleapis.com/css2?family=Noto+Serif:wght@700&family=Open+Sans:wght@400&display=swap" rel="stylesheet">
<style>
  :root {
    --hero-light: #f1f2f3;
    --hero-mid: #d9dcdf;
    --hero-skin: #c9a58c;
    --brand-blue: #4f8cc6;
    --nav-blue: #5d9cd0;
    --nav-divider: rgba(255,255,255,0.28);
    --nav-text: #ffffff;
    --nav-muted: #b9d5ec;
    --accent-green: #8cbb55;
    --caption-bg: rgba(45,45,45,0.88);
    --caption-text: #ffffff;
    --tile-navy: #34456a;
    --tile-grey: #9a9ea3;
    --tile-slate: #7c8794;
  }
  * { margin: 0; padding: 0; box-sizing: border-box; }
  html, body { width: 1200px; height: 644px; overflow: hidden; background: #fff; }
  .page { position: relative; width: 1200px; height: 644px; overflow: hidden; font-family: "Open Sans", sans-serif; }

  .hero-photo {
    position: absolute; inset: 0 0 52px 0;
    background:
      radial-gradient(ellipse 320px 260px at 560px 300px, rgba(201,165,140,0.45), transparent 70%),
      radial-gradient(ellipse 260px 200px at 1050px 90px, rgba(220,225,235,0.8), transparent 70%),
      linear-gradient(135deg, var(--hero-light) 0%, #e6e8ea 45%, var(--hero-mid) 100%);
  }

  .brand {
    position: absolute; left: 54px; top: 46px;
    display: flex; align-items: center; gap: 10px;
    font-family: "Noto Serif", serif; font-weight: 700; font-size: 36px;
    color: var(--brand-blue); letter-spacing: 0.5px;
  }
  .brand-mark { width: 16px; height: 16px; background: var(--brand-blue); }

  .slide-title {
    position: absolute; left: 54px; top: 293px; width: 307px; height: 43px;
    background: var(--caption-bg); color: var(--caption-text);
    font-family: "Noto Serif", serif; font-weight: 700; font-size: 18px;
    line-height: 43px; padding-left: 18px; white-space: pre;
  }
  .slide-text {
    position: absolute; left: 54px; top: 338px; width: 664px; height: 46px;
    background: var(--caption-bg); color: var(--caption-text);
    font-size: 15px; line-height: 46px; padding-left: 20px;
  }

  .feature-tiles { position: absolute; left: 700px; top: 54px; width: 448px; height: 448px; }
  .info-label {
    position: absolute; left: 756px; top: 250px; width: 120px; text-align: center;
    color: #fff; font-size: 19px; line-height: 21px;
  }

  .site-nav {
    position: absolute; left: 0; bottom: 0; width: 1200px; height: 52px;
    background: var(--nav-blue); display: flex; align-items: stretch;
  }
  .site-nav ul { list-style: none; display: flex; padding-left: 41px; }
  .site-nav li { display: flex; align-items: center; padding: 0 13px; font-size: 13.5px; color: var(--nav-text); text-transform: uppercase; border-right: 1px solid var(--nav-divider); }
  .site-nav li:last-child { border-right: none; }
  .copyright { position: absolute; right: 34px; top: 0; line-height: 52px; font-size: 13px; color: var(--nav-muted); }
</style>
</head>
<body>
<div class="page">
  <div class="hero-photo" role="img" aria-label="Photo of hands marking up architectural blueprints with a pencil and ruler"></div>

  <div class="brand"><span class="brand-mark"></span>Tovimar Inc.</div>

  <h1 class="slide-title">Conduct  Placement Lotteries</h1>
  <p class="slide-text">Explain implementation of a lottery and select applicants and keep you out of that process</p>

  <svg class="feature-tiles" viewBox="0 0 448 448" xmlns="http://www.w3.org/2000/svg">
    <polygon points="224,1 330,107 224,213 118,107" fill="var(--tile-navy)" role="img" aria-label="Photo of two engineers in hard hats and safety vests"/>
    <polygon points="332,109 438,215 332,321 226,215" fill="var(--tile-grey)" role="img" aria-label="Photo of hands drafting on a plan"/>
    <polygon points="224,217 330,323 224,429 118,323" fill="var(--tile-slate)" role="img" aria-label="Photo of a construction team in hard hats"/>
    <polygon points="116,109 222,215 116,321 10,215" fill="var(--accent-green)"/>
    <circle cx="114" cy="256" r="8" fill="#fff"/>
    <polyline points="112,252 116,256 112,260" fill="none" stroke="var(--accent-green)" stroke-width="1.8"/>
  </svg>
  <div class="info-label">Get More Information</div>

  <nav class="site-nav">
    <ul>
      <li>Home</li>
      <li>About Company</li>
      <li>Services</li>
      <li>Housing Rehab Application</li>
      <li>Affordable Application</li>
      <li>Contact</li>
    </ul>
    <span class="copyright">©2014</span>
  </nav>
</div>
</body>
</html>
```